Corporate Design für eine Veranstaltungsagentur
Vielen Dank an Bartholomä, der trotz vieler unserer Revisionswünsche stets freundlich war, professionell und schnell gearbeitet hat und uns am Ende ein wirklich wunderbares Ergebnis geliefert hat! :-) Wir können ihn uneingeschränkt weiterempfehlen!
Zielgruppe
Agentur zur Planung, Organisation und Durchführung von Veranstaltungen aller Art
Ingenieurbetrieb für Veranstaltungstechnik und - produktion
Organisation und Durchführung der 'Wellenklang'-Veranstaltungsreihe: www.wellenklang-turnier.de
Zielgruppe:
Personen jeder Altersgruppe, Privatpersonen, Geschäftskunden
Aufgabenstellung
Die Farbe Grün sollte beibehalten werden.
Logo soll Professionalität und Innovation ausstrahlen, gleichzeitig modern und zeitlos wirken.

```html
<!DOCTYPE html>
<html lang="de">
<head>
<meta charset="utf-8">
<title>lumara events – Geschäftsausstattung</title>
<link rel="stylesheet" href="https://fonts.googleapis.com/css2?family=Ubuntu:wght@400;500;700&family=Open+Sans:wght@400;600&display=swap">
<style>
  :root {
    --bg: #2c2d2f;
    --paper: #ffffff;
    --card-dark: #3d3d3b;
    --ink: #2b2b2b;
    --ink-soft: #4a4a4a;
    --green: #7ab51d;
    --rule: #b9b9b9;
  }
  * { box-sizing: border-box; margin: 0; padding: 0; }
  html, body { width: 1200px; height: 856px; overflow: hidden; background: var(--bg); }
  .stage { position: relative; width: 1200px; height: 856px; }

  /* Letterhead */
  .letterhead {
    position: absolute; left: 200px; top: 133px; width: 415px; height: 588px;
    background: var(--paper); font-family: "Ubuntu", sans-serif; color: var(--ink);
  }
  .brand {
    position: absolute; font-family: "Ubuntu", sans-serif; font-weight: 500;
    color: var(--ink-soft); line-height: 0.85; text-align: center;
  }
  .brand .dot { display: block; border-radius: 50%; background: var(--green); margin: 0 auto; }
  .letterhead .brand { left: 323px; top: 32px; font-size: 14px; }
  .letterhead .brand .dot { width: 18px; height: 18px; margin-bottom: 4px; }
  .sender-line {
    position: absolute; left: 44px; top: 91px; width: 124px;
    font-size: 3.6px; color: var(--green); border-bottom: 0.6px solid var(--green); padding-bottom: 1px;
  }
  .recipient { position: absolute; left: 44px; top: 106px; font-size: 6.2px; line-height: 8px; font-style: normal; }
  .recipient .city { margin-top: 8px; }
  .subject { position: absolute; left: 44px; top: 201px; font-size: 6.2px; font-weight: 500; }
  .body-text {
    position: absolute; left: 44px; top: 222px; width: 228px;
    font-size: 6.3px; line-height: 7.55px;
  }
  .body-text .gap { margin-top: 7.55px; }
  .closing { position: absolute; left: 44px; top: 421px; font-size: 5.8px; }
  .signature { position: absolute; left: 44px; top: 433px; width: 88px; height: 14px; background: #e6e6e6; border-radius: 2px; }
  .letter-footer {
    position: absolute; left: 83px; top: 542px; width: 249px; border-top: 0.8px solid var(--green);
    display: flex; justify-content: space-between; padding: 5px 8px 0; font-size: 3.8px; line-height: 5px;
    text-align: center; font-weight: 500;
  }

  /* Business card front */
  .card { position: absolute; width: 254px; height: 163px; }
  .card-front { left: 745px; top: 218px; background: var(--paper); font-family: "Ubuntu", sans-serif; color: var(--ink); }
  .card-front .brand { left: 30px; top: 50px; font-size: 19px; width: 74px; }
  .card-front .brand .dot { width: 26px; height: 26px; margin-bottom: 6px; }
  .card-divider { position: absolute; left: 126px; top: 22px; width: 1px; height: 124px; background: var(--rule); }
  .card-details { position: absolute; left: 136px; top: 36px; width: 96px; text-align: center; font-size: 7px; line-height: 9.4px; }
  .card-details .name { font-weight: 500; }
  .card-details .role { color: var(--green); }
  .card-details .block { margin-top: 6px; }
  .card-details .web { margin-top: 6px; color: var(--green); font-weight: 500; }

  /* Business card back */
  .card-back { left: 747px; top: 475px; background: var(--card-dark); display: flex; align-items: center; justify-content: center; }
  .card-back .brand-inline {
    display: flex; align-items: center; gap: 8px;
    font-family: "Ubuntu", sans-serif; font-weight: 500; font-size: 20px; color: var(--green);
  }
  .card-back .dot { width: 22px; height: 22px; border-radius: 50%; background: var(--green); }
</style>
</head>
<body>
<main class="stage">

  <section class="letterhead">
    <div class="brand"><span class="dot"></span>lumara<br>events</div>

    <div class="sender-line">Vorname Nachname, Hafenweg 12, 28195 Bremen</div>

    <address class="recipient">
      Helene Sommerfeld<br>Lindenallee 27
      <div class="city">10437 Berlin</div>
    </address>

    <div class="subject">Ihre Anfrage vom März, Angebot und Ablauf.</div>

    <div class="body-text">
      <p>Wir planen Veranstaltungen mit Sorgfalt, Erfahrung und einem klaren Blick für jedes Detail. Von der ersten Idee bis zum letzten Gast begleiten wir Sie persönlich und verlässlich. Technik, Bühne, Licht und Ton kommen aus einer Hand, damit Ihr Abend reibungslos gelingt. Gerne stellen wir Ihnen unser Angebot in einem Gespräch vor und beantworten offene Fragen. Unsere Referenzen reichen von Firmenfeiern über Messen bis zu großen öffentlichen Festen. Jede Planung beginnt bei uns mit Zuhören, denn nur so entsteht ein Ereignis, das wirklich zu Ihnen passt. Wir freuen uns auf Ihre Nachricht und auf die gemeinsame Arbeit an Ihrem Projekt, vom ersten Entwurf bis zum fertigen Ablauf.</p>
      <p class="gap">Für Ihre Veranstaltung im Frühjahr haben wir erste Ideen gesammelt, darunter ein flexibles Bühnenkonzept, eine abgestimmte Lichtplanung und ein Ablauf mit genügend Raum für Gäste.</p>
      <p>Auch bei Catering, Dekoration und Anreise unterstützen wir Sie mit bewährten Partnern aus der Region. Unser Team kümmert sich um Genehmigungen, Sicherheit und einen ruhigen Aufbau vor Ort. Während der Veranstaltung ist stets eine feste Ansprechperson für Sie erreichbar. Nach dem Ende sorgen wir für einen zügigen Abbau und werten den Abend gemeinsam mit Ihnen aus. So wächst mit jeder Feier die Erfahrung, von der Ihr nächstes Projekt profitiert. Wir melden uns in den nächsten Tagen telefonisch bei Ihnen, um einen Termin abzustimmen und alle Fragen zu klären.</p>
    </div>

    <div class="closing">Sincerely</div>
    <div class="signature" role="img" aria-label="Handschriftliche Unterschrift"></div>

    <footer class="letter-footer">
      <div>lumara events GmbH<br>Hafenweg 12<br>28195 Bremen</div>
      <div>T: 0421 / 583 920 14<br>F: 0421 / 583 920 15<br>info@beispielnetz.de</div>
      <div>Hansebank AG<br>IBAN: DE44 2905 0101 8273<br>BIC: HNSBDE2BXXX</div>
    </footer>
  </section>

  <section class="card card-front">
    <div class="brand"><span class="dot"></span>lumara<br>events</div>
    <div class="card-divider"></div>
    <div class="card-details">
      <div class="name">Vorname Nachname</div>
      <div class="role">Geschäftsführung</div>
      <div class="block">Hafenweg 12<br>28195 Bremen</div>
      <div class="block">T: 0421 / 583 920 14<br>F: 0421 / 583 920 15<br>info@beispielnetz.de</div>
      <div class="web">www.beispielnetz.de</div>
    </div>
  </section>

  <section class="card card-back">
    <div class="brand-inline"><span class="dot"></span>lumara events</div>
  </section>

</main>
</body>
</html>
```